Need webdesign for service company that provides Car hiring service and transit service

We need a web design for a company that provides airport transit services and transport services including Limo, Corporate cars, Disability transit, Family transit service. We need is a simple and professional design.

Below is site which we like and also offer the same service http://www.ridelarkway.com.au/
Updates

Project Deadline Extended
Reason: Waiting for the Feedback from multiple stakeholders. Need the time to select and approve the design

Target Market(s)

Tourism, Travel

Industry/Entity Type

Airport

Number of Pages Required

3 page

Font styles to use
Decorative
Script

Requirements
Must have
• Simple and Professional, Site we like http://www.ridelarkway.com.au/ and also need to mobile friendly
Should not have
• Shouldn't have too many images

```html
<!DOCTYPE html>
<html lang="en">
<head>
<meta charset="utf-8">
<title>GoLane – Private &amp; Business Transport</title>
<link href="https://fonts.googleapis.com/css2?family=Roboto:wght@300;400;500;700&family=Yellowtail&family=Dancing+Script:wght@700&display=swap" rel="stylesheet">
<style>
:root{
  --ink:#1e1e1e;
  --header:#222222;
  --orange:#e27b0c;
  --navy:#35365a;
  --charcoal:#3d3d3d;
  --text:#555555;
  --light:#f1f1f1;
  --band:#e3e3e3;
  --white:#ffffff;
}
*{margin:0;padding:0;box-sizing:border-box}
html,body{width:1066px;height:1200px;overflow:hidden}
body{position:relative;font-family:'Roboto',sans-serif;color:var(--text);background:linear-gradient(#e6e6e6,var(--light) 200px,var(--light));}
.site-header{position:absolute;left:0;top:0;width:1066px;height:97px;background:var(--header)}
.brand{position:absolute;left:100px;top:30px;display:flex;align-items:center;gap:10px;color:var(--white);font-size:30px;font-weight:300;letter-spacing:1px}
.brand-mark{width:26px;height:26px;border:2px solid var(--white)}
.header-tools{position:absolute;right:99px;top:34px;display:flex;align-items:center;gap:14px}
.header-tools svg{width:18px;height:18px}
.login{margin-left:16px;width:78px;height:31px;background:var(--orange);color:var(--white);font-size:12px;font-weight:500;display:flex;align-items:center;justify-content:center}
.intro{position:absolute;left:99px;top:136px;width:868px;text-align:center}
.intro h1{font-family:'Yellowtail','Dancing Script',cursive;font-weight:400;font-size:42px;color:var(--ink);line-height:1;height:44px}
.intro h2{margin-top:12px;font-size:14px;font-weight:500;letter-spacing:2.2px;color:#555}
.intro p{margin-top:22px;font-size:12px;line-height:18.5px;color:#666}
.tile{position:absolute;color:var(--white);font-size:13px;font-weight:300;line-height:15px;padding:0 14px 12px;display:flex;align-items:flex-end;text-transform:uppercase}
.tile b{font-weight:500}
.quote{position:absolute;left:99px;top:313px;width:284px;height:345px;background:linear-gradient(#555,#3b3b3b);padding:20px 22px;color:var(--white)}
.quote h3{font-size:17px;font-weight:500}
.field{margin-top:14px;height:35px;background:var(--white);display:flex;align-items:center}
.field + .field{margin-top:8px}
.field i{width:36px;height:35px;background:#ececec;display:flex;align-items:center;justify-content:center;flex:none}
.field span{padding-left:9px;font-size:12px;color:#999;white-space:nowrap;overflow:hidden}
.opt{margin-top:14px;font-size:12px;display:flex;align-items:center;gap:5px}
.opt + .opt{margin-top:10px}
.estimate{margin-top:20px;height:58px;background:var(--orange);font-size:18px;font-weight:700;display:flex;align-items:center;justify-content:center}
.note{margin-top:10px;text-align:center;font-size:11.5px}
.grid-shadow{position:absolute;left:80px;top:680px;width:906px;height:20px;border-radius:50%;background:radial-gradient(ellipse at center,rgba(0,0,0,.18),rgba(0,0,0,0) 70%)}
.band{position:absolute;left:0;top:742px;width:1066px;height:420px;background:linear-gradient(#e0e0e0,#ebebeb)}
.band-notch{position:absolute;left:517px;top:742px;width:0;height:0;border-left:16px solid transparent;border-right:16px solid transparent;border-top:16px solid var(--light)}
.feature{position:absolute;top:800px;width:160px;text-align:center;font-size:12px;line-height:17px;color:#555}
.feature svg{display:block;margin:0 auto 10px;width:36px;height:34px}
.panel{position:absolute;top:974px;height:142px;padding:20px 22px;color:var(--white)}
.panel h4{font-size:14px;font-weight:500}
.news{left:99px;width:423px;background:var(--charcoal)}
.news p{margin-top:10px;font-size:12px;line-height:17px;color:#bbb}
.read-more{margin-top:12px;display:inline-block;background:var(--white);color:var(--ink);font-size:12px;padding:8px 13px}
.payment{left:545px;width:422px;background:var(--navy)}
.payment-pointer{position:absolute;left:691px;top:954px;border-left:20px solid transparent;border-right:20px solid transparent;border-bottom:20px solid var(--navy)}
.cards{margin-top:14px;display:flex;align-items:center;gap:14px}
.card{width:49px;height:32px;background:var(--white);border-radius:2px}
.site-footer{position:absolute;left:0;top:1162px;width:1066px;height:38px;background:var(--header);font-size:12px;color:#aaa;display:flex;align-items:center;justify-content:space-between;padding:0 99px}
.site-footer nav span{margin:0 6px}
</style>
</head>
<body>
<header class="site-header">
  <div class="brand"><span class="brand-mark"></span>GOLANE</div>
  <div class="header-tools">
    <svg viewBox="0 0 18 18"><path d="M2 4h14M2 9h14M2 14h14" stroke="#fff" stroke-width="2"/></svg>
    <svg viewBox="0 0 18 18"><path d="M4 2l3 0 1 4-2 1.5a9 9 0 0 0 4.5 4.5L12 10l4 1v3c0 1-1 2-2 2C8 16 2 10 2 4c0-1 1-2 2-2z" fill="#fff"/></svg>
    <svg viewBox="0 0 18 18"><circle cx="7.5" cy="7.5" r="5" fill="none" stroke="#fff" stroke-width="2"/><path d="M11 11l5 5" stroke="#fff" stroke-width="2.4"/></svg>
    <div class="login">LOGIN</div>
  </div>
</header>

<section class="intro">
  <h1>Private &amp; Business</h1>
  <h2>PERSONALISED TRANSPORT SERVICE</h2>
  <p>Nam nec tellus a odio tincidunt auctor a ornare odio. Sed non mauris vitae erat consequat auctor eu in elit. Class aptent taciti sociosqu ad litora torquent per conubia nostra, per inceptos himenaeos. Mauris in erat justo. Nullam ac urna eu felis dapibus condimentum sit amet a augue. Sed non neque elit. Sed ut imperdiet nisi. Proin velit mauris egestas quam, ut aliquam massa nisl quis neque. Suspendisse in orci enim.</p>
</section>

<form class="quote">
  <h3>GET INSTANT QUOTE</h3>
  <div class="field"><i><svg width="12" height="12"><circle cx="6" cy="6" r="5" fill="none" stroke="#222" stroke-width="1.5"/></svg></i><span>Origin (Public location or exact ad</span></div>
  <div class="field"><i><svg width="10" height="13" viewBox="0 0 10 13"><path d="M5 0a4.5 4.5 0 0 0-4.5 4.5C.5 8 5 13 5 13s4.5-5 4.5-8.5A4.5 4.5 0 0 0 5 0z" fill="#222"/><circle cx="5" cy="4.5" r="1.6" fill="#ececec"/></svg></i><span>Destination (Public location or ex</span></div>
  <div class="opt"><svg width="11" height="11"><path d="M5.5 0v11M0 5.5h11" stroke="#fff" stroke-width="1.5"/></svg>Add Stops</div>
  <div class="opt"><svg width="12" height="12"><circle cx="6" cy="6" r="5" fill="none" stroke="#fff" stroke-width="1.4"/><circle cx="6" cy="6" r="2.4" fill="#fff"/></svg>Show Other Vehicles</div>
  <div class="estimate">ESATIMATE FARE</div>
  <div class="note">* See price guide for extra</div>
</form>

<div class="tile" role="img" aria-label="Team of hands joined together" style="left:390px;top:313px;width:285px;height:81px;background:linear-gradient(90deg,#3a3b62,#2e2f4e)">BECOME A&nbsp;<b>MEMBER</b></div>
<div class="tile" role="img" aria-label="Information signs in greyscale" style="left:390px;top:402px;width:139px;height:168px;background:linear-gradient(135deg,#5a5a5a,#3e3e3e)"><span>FAQ'S &amp;<br><b>VIDEO<br>TUTORIALS</b></span></div>
<div class="tile" role="img" aria-label="Traveller walking through terminal" style="left:537px;top:402px;width:138px;height:80px;background:linear-gradient(#e9e9e9,#c9c9c9);color:var(--ink)"><span><b>AIRPORT</b><br>MEETING POINTS</span></div>
<div class="tile" role="img" aria-label="Executive assistant at work" style="left:537px;top:490px;width:138px;height:80px;background:linear-gradient(135deg,#3c3d66,#2b2c4a)"><span><b>EXECUTIVE</b><br>ASSISTANTS</span></div>
<div class="tile" role="img" aria-label="Business travellers walking with luggage at airport" style="left:682px;top:313px;width:285px;height:257px;background:linear-gradient(160deg,#c98a44,#b9a48a 35%,#8c8680 70%,#6d6d6d);font-size:19px;line-height:19px;letter-spacing:2px;font-weight:700;padding:0 22px 20px"><span>AIRPORT<br>TRANSFERS</span></div>
<div class="tile" role="img" aria-label="Aircraft at airport gate" style="left:390px;top:578px;width:285px;height:80px;background:linear-gradient(#dadada,#bcbcbc);color:var(--ink)"><span><b>ABOUT</b> GOLANE</span></div>
<div class="tile" role="img" aria-label="Chauffeur driving" style="left:682px;top:578px;width:139px;height:80px;background:linear-gradient(135deg,#595959,#3d3d3d)"><span><b>BECOME</b><br>A DRIVER</span></div>
<div class="tile" role="img" aria-label="Customer support team with headsets" style="left:829px;top:578px;width:138px;height:80px;background:linear-gradient(135deg,#3f4068,#2d2e4c)"><span><b>CONTACT</b><br>TODAY NOW</span></div>

<div class="grid-shadow"></div>
<div class="band"></div>
<div class="band-notch"></div>

<div class="feature" style="left:97px"><svg viewBox="0 0 36 34"><rect x="2" y="8" width="32" height="24" rx="2" fill="#222"/><rect x="12" y="3" width="12" height="6" fill="none" stroke="#222" stroke-width="2.5"/><path d="M2 14l16 8 16-8" stroke="#e3e3e3" stroke-width="2" fill="none"/></svg>Executive chauffeur service and airport transfers &amp; corporate limo hire</div>
<div class="feature" style="left:274px"><svg viewBox="0 0 36 34"><path d="M5 12l7-5 3 2 3-5 5 1 2 6 5 5 3 6-3 7-8 1-4-3-6 1-7 2-2-8z" fill="#222"/></svg>Limousine hire and executive airport transfers across all of Australia</div>
<div class="feature" style="left:453px"><svg viewBox="0 0 36 34"><circle cx="18" cy="17" r="14.5" fill="none" stroke="#222" stroke-width="3"/><path d="M18 8v9l6 5" stroke="#222" stroke-width="3" fill="none"/></svg>Real time booking and confirmation system for all of your limousine services</div>
<div class="feature" style="left:631px"><svg viewBox="0 0 36 34"><path d="M2 11h7l13 13h8M2 24h7l5-5M22 11h8" stroke="#222" stroke-width="3" fill="none"/><path d="M28 5l6 6-6 6zM28 18l6 6-6 6z" fill="#222"/></svg>The only Australian owned and operated limousine service with a streamlined and secure virtual payment and invoicing system</div>
<div class="feature" style="left:809px"><svg viewBox="0 0 36 34"><rect x="2" y="4" width="32" height="26" rx="2" fill="none" stroke="#222" stroke-width="2.5"/><rect x="2" y="10" width="32" height="5" fill="#222"/><rect x="6" y="21" width="10" height="3" fill="#222"/></svg>No credit card surcharge on any of our limousine hire services</div>

<section class="panel news">
  <h4>NEWS AND EVENTS</h4>
  <p>Nullam ac urna eu felis dapibus condimentum sit amet a augue. Sed aliquam massa nisl quis neque. Suspendisse in orci enim.</p>
  <span class="read-more">READ MORE</span>
</section>
<div class="payment-pointer"></div>
<section class="panel payment">
  <h4>SECURE ONLINE PAYMENT</h4>
  <div class="cards">
    <svg width="42" height="48" viewBox="0 0 42 48"><path d="M11 20v-7a10 10 0 0 1 20 0v7" fill="none" stroke="#fff" stroke-width="4"/><rect x="3" y="20" width="36" height="26" rx="6" fill="none" stroke="#fff" stroke-width="3"/><text x="21" y="39" text-anchor="middle" fill="#fff" font-family="Roboto,sans-serif" font-size="12" font-weight="500">SSL</text></svg>
    <span class="card"></span><span class="card"></span><span class="card"></span>
  </div>
</section>

<footer class="site-footer">
  <div>© Copyright 2017 GoLane. All Rights Reserved</div>
  <nav>Home<span>|</span>Sitemap<span>|</span>Privacy Policy<span>|</span>Terms &amp; Conditions</nav>
</footer>
</body>
</html>
```